A start-up named "Corvane Therapeutics" - needs a new PowerPoint design

We need a new PowerPoint Design for an early-stage start-up named "Corvane Therapeutics" seeking to disrupt the current approach towards drug discovery within aging disorders.

We would like to build on Corvane's legacy, the founder of the modern science of genetics, by employing a multidisciplinary approach, experimenting, and providing elderly patients the attention they deserve.

We have selected the suffix "therapeutics" intentionally as it stands for (a medicine) the treatment of disease; the science of healing. Alzheimer’s treatment is a huge, urgent, unmet need:
- Shift from a disease-management system to a preventive medicine system
- Focus on increasing the health span, not only the life span

Target Market(s)

Pharma/ Biotech Executives Medical Institutions Healthcare professionals (MDs, nurses, payors, pharmacists, etc.) Patients

Industry/Entity Type

Healthcare

Other font styles liked:
• Celias

Colors
0054AA
0677BA
7BADD7
CADEEF
E8F1F8
E54698
E96AAD
F1A4CE
F9D9EA
FCEFF6
A7469A
B969AE
D3A5CF
EDDBEB
F8F0F9
6B429C
8869AF
B7A5CE
E3DAEB
F3F0F8

Requirements
Must have
• - differentiate from other companies named after Corvane - differentiate from other Pharma/ Biotech companies
Nice to have
• simplicity/ minimalist logo vivid colors gradient 3D Life-Sciences inspired Simple geometry Balance
Should not have
• mascot/ emblem watermark logo animated ink style nature-inspired inventive typography artistic chaos

```html
<!DOCTYPE html>
<html lang="en">
<head>
<meta charset="utf-8">
<title>Corvane Therapeutics – Presentation Template, Part 1</title>
<link href="https://fonts.googleapis.com/css2?family=Outfit:wght@400;500;600;700&display=swap" rel="stylesheet">
<style>
  :root {
    --blue-deep: #0054AA;
    --blue: #0677BA;
    --blue-light: #7BADD7;
    --pink: #E54698;
    --magenta: #C2217E;
    --plum: #A7469A;
    --purple: #6B429C;
    --navy: #0c3a78;
    --canvas: #f2f2f2;
    --ink: #1d1d26;
    --rule: #d6d6de;
    --part-blue: #0a14f0;
    --brand-grad: linear-gradient(90deg, #c63d82 0%, #8b46aa 100%);
  }
  * { box-sizing: border-box; margin: 0; padding: 0; }
  html, body { width: 1200px; height: 1200px; overflow: hidden; }
  body {
    background: var(--canvas);
    font-family: "Outfit", sans-serif;
    color: var(--ink);
    position: relative;
  }
  .slide {
    position: absolute;
    width: 562px;
    height: 316px;
    background: #fff;
    overflow: hidden;
  }
  .slide--title { left: 32px; top: 30px; }
  .slide--style { left: 610px; top: 30px; }
  .slide--about { left: 32px; top: 361px; }
  .slide--team { left: 610px; top: 361px; }
  .slide--chart { left: 32px; top: 692px; }
  .slide--services { left: 610px; top: 692px; }

  .slide__topbar {
    position: absolute; left: 0; top: 0; width: 100%; height: 3px;
    background: var(--brand-grad);
  }
  .slide__heading {
    position: absolute; left: 18px; top: 20px;
    font-size: 19px; font-weight: 600; color: var(--blue-deep);
    letter-spacing: 0.1px;
  }
  .footer-brand {
    position: absolute; left: 18px; bottom: 9px;
    font-size: 10.5px; font-weight: 500; color: var(--blue);
    line-height: 1;
  }
  .footer-badge {
    position: absolute; right: 0; bottom: 0; width: 144px; height: 21px;
  }
  .footer-badge svg { position: absolute; inset: 0; }
  .footer-badge__text {
    position: absolute; right: 8px; top: 0; height: 21px; line-height: 21px;
    font-size: 5.8px; color: #fff; white-space: nowrap;
  }
  .footer-badge__text b { font-weight: 600; margin-left: 3px; padding-left: 4px; border-left: 0.8px solid #fff; }

  .sect-title { font-weight: 600; color: var(--blue-deep); }

  /* Title slide */
  .title-art { position: absolute; inset: 0; }
  .title-brand {
    position: absolute; left: 22px; top: 90px;
    font-size: 19px; font-weight: 500; color: var(--blue-deep); line-height: 1.05;
  }
  .title-main {
    position: absolute; left: 20px; top: 176px;
    font-size: 29px; font-weight: 600; color: #fff; white-space: nowrap;
  }
  .title-sub {
    position: absolute; left: 20px; top: 216px;
    font-size: 13px; font-weight: 600; color: #fff;
  }
  .title-rule {
    position: absolute; left: 20px; top: 242px; width: 274px; height: 1px;
    background: rgba(255,255,255,0.7);
  }
  .title-lede {
    position: absolute; left: 20px; top: 251px;
    font-size: 9.4px; color: #fff; white-space: nowrap;
  }

  /* Template style slide */
  .bullets { position: absolute; left: 18px; top: 66px; width: 520px; list-style: none; }
  .bullets > li {
    position: relative; padding-left: 8px;
    font-size: 12.2px; line-height: 14.2px;
  }
  .bullets > li::before {
    content: "•"; position: absolute; left: 0; top: 0; color: var(--pink); font-size: 10px;
  }
  .bullets ul { list-style: none; margin-top: 5px; }
  .bullets ul li {
    position: relative; padding-left: 8px;
    font-size: 10.5px; line-height: 12.6px;
  }
  .bullets ul li::before { content: "-"; position: absolute; left: 0; color: var(--pink); }

  /* About slide */
  .about-band {
    position: absolute; left: 0; top: 58px; width: 100%; height: 124px;
    background: linear-gradient(90deg, #c8477f 0%, #a84b97 50%, #8650b5 100%);
    color: #fff; text-align: center;
    display: flex; flex-direction: column; justify-content: center; align-items: center;
  }
  .about-band__title { font-size: 15px; font-weight: 600; margin-bottom: 2px; }
  .about-band__text { font-size: 12.4px; line-height: 15.6px; }
  .about-cols { position: absolute; left: 0; top: 201px; width: 100%; display: flex; }
  .about-col {
    flex: 1; text-align: center; height: 66px; padding-top: 5px;
  }
  .about-col + .about-col { border-left: 1px solid var(--rule); }
  .about-col .sect-title { font-size: 12.5px; }
  .about-col p { font-size: 8.3px; line-height: 9.9px; margin-top: 1px; }

  /* Team slide */
  .team-card {
    position: absolute; top: 66px; width: 161px; height: 198px;
  }
  .team-card__photo { position: absolute; left: 0; top: 0; width: 161px; height: 158px; }
  .team-card__label {
    position: absolute; left: 0; top: 158px; width: 161px; height: 40px;
    background: linear-gradient(90deg, #c2447f 0%, #8d47b0 100%);
    color: #fff; text-align: center; padding-top: 8px;
  }
  .team-card__name { font-size: 11px; font-weight: 600; line-height: 13px; }
  .team-card__role { font-size: 9px; line-height: 11px; }

  /* Chart slide */
  .chart-copy { position: absolute; left: 18px; width: 240px; }
  .chart-copy .sect-title { font-size: 12.5px; line-height: 15px; }
  .chart-copy p { font-size: 9.3px; line-height: 11.2px; margin-top: 2px; }
  .chart-rule { position: absolute; left: 18px; top: 163px; width: 238px; height: 1px; background: var(--rule); }
  .chart-divider { position: absolute; left: 290px; top: 65px; width: 1px; height: 211px; background: var(--rule); }
  .chart-title {
    position: absolute; left: 319px; width: 200px; top: 70px; text-align: center;
    font-size: 10.5px; font-weight: 600; color: var(--blue-deep);
  }
  .chart-donut { position: absolute; left: 339px; top: 90px; }
  .chart-legend {
    position: absolute; left: 319px; width: 200px; top: 255px;
    display: flex; justify-content: center; gap: 7px;
    font-size: 7.8px; color: #555;
  }
  .chart-legend span::before {
    content: ""; display: inline-block; width: 4px; height: 4px; margin-right: 2px;
    background: var(--swatch); vertical-align: 1px;
  }

  /* Services slide */
  .service {
    position: absolute; top: 66px; width: 127px; height: 166px;
    border: 1px solid var(--rule); text-align: center;
  }
  .service__icon { position: absolute; left: 43px; top: 18px; width: 40px; height: 40px; }
  .service__rule { position: absolute; left: 10px; right: 10px; top: 75px; height: 1px; background: var(--rule); }
  .service__body { position: absolute; left: 0; right: 0; top: 83px; }
  .service .sect-title { font-size: 12.5px; line-height: 15px; }
  .service p { font-size: 9.4px; line-height: 11.2px; margin-top: 1px; }
  .services-note {
    position: absolute; left: 14px; right: 14px; top: 243px; text-align: center;
    font-size: 9.4px; line-height: 11.4px;
  }

  /* Part label */
  .part-label {
    position: absolute; left: 0; top: 1068px; width: 458px; height: 108px;
    background: var(--part-blue); color: #fff;
    font-family: "Outfit", sans-serif; font-weight: 700; font-size: 92px;
    line-height: 108px; padding-left: 48px; letter-spacing: 1px;
  }
</style>
</head>
<body>

<!-- Slide 1: Title -->
<section class="slide slide--title">
  <svg class="title-art" viewBox="0 0 562 316" width="562" height="316" aria-hidden="true">
    <defs>
      <linearGradient id="titleBlue" x1="0" y1="1" x2="1" y2="0">
        <stop offset="0" stop-color="#0c3a78"/>
        <stop offset="1" stop-color="#2f8ff0"/>
      </linearGradient>
      <linearGradient id="titlePurple" x1="0" y1="0" x2="1" y2="1">
        <stop offset="0" stop-color="#7a3aa6"/>
        <stop offset="1" stop-color="#c23a80"/>
      </linearGradient>
      <linearGradient id="labScene" x1="0" y1="0" x2="1" y2="1">
        <stop offset="0" stop-color="#dfe9f2"/>
        <stop offset="0.5" stop-color="#c9dcea"/>
        <stop offset="1" stop-color="#eef3f7"/>
      </linearGradient>
    </defs>
    <polygon points="205,0 562,0 562,316 412,316" fill="url(#labScene)" role="img" aria-label="Photo of scientists in masks working with test tubes in a laboratory"/>
    <line x1="200" y1="130" x2="372" y2="0" stroke="#d5d9e0" stroke-width="2"/>
    <polygon points="111,0 205,0 412,316 382,316" fill="url(#titlePurple)"/>
    <polygon points="0,146 254,146 384,296 0,296" fill="url(#titleBlue)"/>
  </svg>
  <div class="title-brand">Corvane<br>Therapeutics</div>
  <h1 class="title-main">Presentation Title</h1>
  <div class="title-sub">Subtitle Goes Here</div>
  <div class="title-rule"></div>
  <div class="title-lede">Lorem ipsum dolor sit amet, consectetur adipiscing elit.</div>
</section>

<!-- Slide 2: Template Style -->
<section class="slide slide--style">
  <div class="slide__topbar"></div>
  <h2 class="slide__heading">Template Style</h2>
  <ul class="bullets">
    <li>Lorem ipsum dolor sit amet, consectetur adipiscing elit. Curabitur at fringilla velit. In ac sagittis nulla. Nulla quis erat et ligula aliquam sagittis in viverra mauris. Pellentesque pharetra hendrerit orci at.
      <ul>
        <li>Donec vel suscipit purus, ultrices ornare neque. Sed nec est a lacus lacinia venenatis non at est. Vestibulum vitae lorem lectus. Phasellus gravida mauris a sapien elementum malesuada. Vestibulum ut urna eu dolor suscipit condimentum. Curabitur sed commodo leo. Phasellus faucibus sem ante.</li>
      </ul>
    </li>
  </ul>
  <div class="footer-brand">Corvane</div>
  <div class="footer-badge">
    <svg viewBox="0 0 144 21" width="144" height="21" aria-hidden="true"><polygon points="0,21 14,0 144,0 144,21" fill="#0054AA"/><polygon points="9,21 23,0 144,0 144,21" fill="url(#badgeGrad)"/><defs><linearGradient id="badgeGrad"><stop offset="0" stop-color="#c63d82"/><stop offset="1" stop-color="#8b46aa"/></linearGradient></defs></svg>
    <div class="footer-badge__text">Copywrite Statement 2022<b>2</b></div>
  </div>
</section>

<!-- Slide 3: About Us -->
<section class="slide slide--about">
  <div class="slide__topbar"></div>
  <h2 class="slide__heading">About Us</h2>
  <div class="about-band" role="img" aria-label="Pink to purple band over a soft molecular background">
    <div class="about-band__title">Section Header</div>
    <div class="about-band__text">Lorem ipsum dolor sit amet, consectetur adipiscing elit. Curabitur at fringilla velit.<br>In ac sagittis nulla. Nulla quis erat et ligula aliquam sagittis in viverra mauris.</div>
  </div>
  <div class="about-cols">
    <div class="about-col"><div class="sect-title">Section Header</div><p>Lorem ipsum dolor sit amet,<br>consectetur at es adipiscing elit.<br>Curabitur fringilla velit.</p></div>
    <div class="about-col"><div class="sect-title">Section Header</div><p>Lorem ipsum dolor sit amet,<br>consectetur at es adipiscing elit.<br>Curabitur fringilla velit.</p></div>
    <div class="about-col"><div class="sect-title">Section Header</div><p>Lorem ipsum dolor sit amet,<br>consectetur at es adipiscing elit.<br>Curabitur fringilla velit.</p></div>
  </div>
  <div class="footer-brand">Corvane</div>
  <div class="footer-badge">
    <svg viewBox="0 0 144 21" width="144" height="21" aria-hidden="true"><polygon points="0,21 14,0 144,0 144,21" fill="#0054AA"/><polygon points="9,21 23,0 144,0 144,21" fill="url(#badgeGrad)"/></svg>
    <div class="footer-badge__text">Copywrite Statement 2022<b>3</b></div>
  </div>
</section>

<!-- Slide 4: Meet Our Team -->
<section class="slide slide--team">
  <div class="slide__topbar"></div>
  <h2 class="slide__heading">Meet Our Team</h2>
  <div class="team-card" style="left:17px">
    <div class="team-card__photo" role="img" aria-label="Portrait photo of a team member" style="background:linear-gradient(160deg,#8aa35a 0%,#6f7f4a 55%,#b9987a 100%)"></div>
    <div class="team-card__label"><div class="team-card__name">Enter Name Here</div><div class="team-card__role">Subtitle</div></div>
  </div>
  <div class="team-card" style="left:201px">
    <div class="team-card__photo" role="img" aria-label="Portrait photo of a team member" style="background:linear-gradient(170deg,#d8dbe0 0%,#b8bcc4 60%,#e6e8ec 100%)"></div>
    <div class="team-card__label"><div class="team-card__name">Enter Name Here</div><div class="team-card__role">Subtitle</div></div>
  </div>
  <div class="team-card" style="left:384px">
    <div class="team-card__photo" role="img" aria-label="Portrait photo of a team member" style="background:linear-gradient(170deg,#c9ccd4 0%,#a88470 55%,#3d5a80 100%)"></div>
    <div class="team-card__label"><div class="team-card__name">Enter Name Here</div><div class="team-card__role">Subtitle</div></div>
  </div>
  <div class="footer-brand">Corvane</div>
  <div class="footer-badge">
    <svg viewBox="0 0 144 21" width="144" height="21" aria-hidden="true"><polygon points="0,21 14,0 144,0 144,21" fill="#0054AA"/><polygon points="9,21 23,0 144,0 144,21" fill="url(#badgeGrad)"/></svg>
    <div class="footer-badge__text">Copywrite Statement 2022<b>4</b></div>
  </div>
</section>

<!-- Slide 5: Chart with Content -->
<section class="slide slide--chart">
  <div class="slide__topbar"></div>
  <h2 class="slide__heading">Chart with Content</h2>
  <div class="chart-copy" style="top:76px">
    <div class="sect-title">Section Header</div>
    <p>Donec vel suscipit purus, ultrices ornare neque. Sed nec est a lacus lacinia venenatis non at est. Vestibulum vitae lorem lectus. Phasellus gravida mauris a sapien elementum malesuada. Vestibulum ut urna eu dolor.</p>
  </div>
  <div class="chart-rule"></div>
  <div class="chart-copy" style="top:178px">
    <div class="sect-title">Section Header</div>
    <p>Lorem ipsum dolor sit amet, consectetur adipiscing elit. Curabitur at fringilla velit. In ac sagittis nulla. Nulla quis erat et ligula aliquam sagittis in viverra mauris. Pellentesque pharetra hendrerit orci at.</p>
  </div>
  <div class="chart-divider"></div>
  <div class="chart-title">Sales</div>
  <svg class="chart-donut" viewBox="0 0 160 160" width="160" height="160" role="img" aria-label="Donut chart of sales by quarter">
    <g transform="rotate(-90 80 80)" fill="none" stroke-width="23">
      <circle cx="80" cy="80" r="67" stroke="#0054AA" stroke-dasharray="240 421"/>
      <circle cx="80" cy="80" r="67" stroke="#0677BA" stroke-dasharray="105 421" stroke-dashoffset="-241"/>
      <circle cx="80" cy="80" r="67" stroke="#7BADD7" stroke-dasharray="40 421" stroke-dashoffset="-347"/>
      <circle cx="80" cy="80" r="67" stroke="#E54698" stroke-dasharray="33 421" stroke-dashoffset="-388"/>
    </g>
    <g stroke="#fff" stroke-width="1.2">
      <line x1="80" y1="2" x2="80" y2="35"/>
    </g>
  </svg>
  <div class="chart-legend">
    <span style="--swatch:#0054AA">1st Qtr</span>
    <span style="--swatch:#0677BA">2nd Qtr</span>
    <span style="--swatch:#7BADD7">3rd Qtr</span>
    <span style="--swatch:#E54698">4th Qtr</span>
  </div>
  <div class="footer-brand">Corvane</div>
  <div class="footer-badge">
    <svg viewBox="0 0 144 21" width="144" height="21" aria-hidden="true"><polygon points="0,21 14,0 144,0 144,21" fill="#0054AA"/><polygon points="9,21 23,0 144,0 144,21" fill="url(#badgeGrad)"/></svg>
    <div class="footer-badge__text">Copywrite Statement 2022<b>5</b></div>
  </div>
</section>

<!-- Slide 6: Medical Services -->
<section class="slide slide--services">
  <div class="slide__topbar"></div>
  <h2 class="slide__heading">Medical Services</h2>

  <div class="service" style="left:17px">
    <svg class="service__icon" viewBox="0 0 40 40" aria-hidden="true">
      <rect x="9" y="3" width="24" height="34" rx="2" fill="#C2217E"/>
      <rect x="6" y="8" width="4" height="2" fill="#C2217E"/><rect x="6" y="15" width="4" height="2" fill="#C2217E"/><rect x="6" y="22" width="4" height="2" fill="#C2217E"/><rect x="6" y="29" width="4" height="2" fill="#C2217E"/>
      <circle cx="20" cy="12" r="4.5" fill="none" stroke="#fff" stroke-width="1.3"/>
      <path d="M20 9.5v5M17.5 12h5" stroke="#fff" stroke-width="1.3"/>
      <path d="M14 21h13M14 25h13M14 29h13" stroke="#fff" stroke-width="1.3"/>
    </svg>
    <div class="service__rule"></div>
    <div class="service__body"><div class="sect-title">Section Header</div><p>Lorem ipsum dolor sit<br>amet, consectetur at<br>es adipiscing elit.<br>Curabitur fringilla</p></div>
  </div>

  <div class="service" style="left:149px">
    <svg class="service__icon" viewBox="0 0 40 40" aria-hidden="true">
      <path d="M6 15h8v17a4 4 0 0 1-8 0z" fill="#C2217E"/>
      <rect x="5" y="13" width="10" height="2.5" fill="#C2217E"/>
      <path d="M23 6h8v10l7 17a3 3 0 0 1-3 4H19a3 3 0 0 1-3-4l7-17z" fill="#C2217E"/>
      <rect x="21" y="3" width="12" height="3" fill="#C2217E"/>
      <path d="M20 30l4-8" stroke="#fff" stroke-width="1.5"/>
    </svg>
    <div class="service__rule"></div>
    <div class="service__body"><div class="sect-title">Section Header</div><p>Lorem ipsum dolor sit<br>amet, consectetur at<br>es adipiscing elit.<br>Curabitur fringilla</p></div>
  </div>

  <div class="service" style="left:281px">
    <svg class="service__icon" viewBox="0 0 40 40" aria-hidden="true">
      <g stroke="#C2217E" stroke-width="2.4">
        <path d="M20 2v8M20 30v8M2 20h8M30 20h8M7 7l6 6M27 27l6 6M33 7l-6 6M13 27l-6 6"/>
      </g>
      <circle cx="20" cy="20" r="12" fill="#C2217E"/>
      <circle cx="16" cy="16" r="2.5" fill="#fff"/><circle cx="24" cy="17" r="2" fill="#fff"/><circle cx="19" cy="24" r="2.2" fill="#fff"/><circle cx="25" cy="24" r="1.5" fill="#fff"/>
    </svg>
    <div class="service__rule"></div>
    <div class="service__body"><div class="sect-title">Section Header</div><p>Lorem ipsum dolor sit<br>amet, consectetur at<br>es adipiscing elit.<br>Curabitur fringilla</p></div>
  </div>

  <div class="service" style="left:412px">
    <svg class="service__icon" viewBox="0 0 40 40" aria-hidden="true">
      <g transform="rotate(35 25 15)"><rect x="14" y="9" width="24" height="12" rx="6" fill="#C2217E"/><rect x="26" y="9" width="1.5" height="12" fill="#fff"/></g>
      <circle cx="12" cy="28" r="7" fill="#C2217E"/>
      <path d="M7 33l10-10" stroke="#fff" stroke-width="1.5"/>
    </svg>
    <div class="service__rule"></div>
    <div class="service__body"><div class="sect-title">Section Header</div><p>Lorem ipsum dolor sit<br>amet, consectetur at<br>es adipiscing elit.<br>Curabitur fringilla</p></div>
  </div>

  <p class="services-note">Lorem ipsum dolor sit amet, consectetur adipiscing elit. Curabitur at fringilla velit. In ac sagittis nulla. Nulla quis erat et ligula aliquam sagittis in viverra mauris. Pellentesque pharetra hendrerit orci at. Phasellus gravida mauris.</p>
  <div class="footer-brand">Corvane</div>
  <div class="footer-badge">
    <svg viewBox="0 0 144 21" width="144" height="21" aria-hidden="true"><polygon points="0,21 14,0 144,0 144,21" fill="#0054AA"/><polygon points="9,21 23,0 144,0 144,21" fill="url(#badgeGrad)"/></svg>
    <div class="footer-badge__text">Copywrite Statement 2022<b>6</b></div>
  </div>
</section>

<div class="part-label">PART 1</div>

</body>
</html>
```